Full re-design of visual identity

We have just re-designed our logo and would like to apply it on our folders, business cards, stationery, and etc... we are attaching new logo + the material we need to re-design... we will provide full corel draw files to help make job easier and also because lot of icons and artwork can be still used...

any doubts we are at your disposal. thanks in advance.

```html
<!DOCTYPE html>
<html lang="en">
<head>
<meta charset="utf-8">
<title>Lumora – Folder and Letterhead</title>
<link href="https://fonts.googleapis.com/css2?family=Exo+2:wght@400;600;700&family=Open+Sans:wght@400;600&display=swap" rel="stylesheet">
<style>
  :root{
    --bg:#f1f1f1;
    --folder-top:#6a6a6a;
    --folder-bottom:#4a4a4a;
    --orange:#ee7a2c;
    --text-grey:#7a7a7a;
    --folder-name:#c4c4c4;
    --letter-name:#6a6a6a;
    --line:#6d6d6d;
    --paper:#ffffff;
  }
  *{box-sizing:border-box;margin:0;padding:0}
  html,body{width:1200px;height:1000px;overflow:hidden;background:var(--bg)}
  body{position:relative;font-family:"Open Sans",Arial,sans-serif;color:var(--text-grey)}

  /* Folder cover */
  .folder{
    position:absolute;left:60px;top:120px;width:500px;height:720px;
    background:linear-gradient(160deg,var(--folder-top),var(--folder-bottom));
    overflow:hidden;box-shadow:0 6px 18px rgba(0,0,0,.18);
  }
  .company-name{
    font-family:"Open Sans",Arial,sans-serif;font-weight:600;line-height:1;
    white-space:nowrap;
  }
  .folder .company-name{
    position:absolute;left:0;right:0;top:270px;text-align:center;
    font-size:64px;color:var(--folder-name);
  }
  .folder .swoop{position:absolute;left:0;bottom:0;width:500px;height:200px}
  .folder .contact{position:absolute;left:34px;top:440px;font-size:9px;color:#9a9a9a;line-height:15px}

  .contact-row{display:flex;align-items:flex-start;gap:7px}
  .contact-row svg{flex:none;margin-top:3px}

  /* Letterhead */
  .letterhead{
    position:absolute;left:620px;top:110px;width:520px;height:740px;
    background:var(--paper);box-shadow:0 6px 18px rgba(0,0,0,.12);
  }
  .meta{position:absolute;left:40px;top:44px;font-size:9px;line-height:11px}
  .meta dt{font-family:"Exo 2",Arial,sans-serif;font-weight:700;color:var(--orange);text-transform:uppercase;font-size:10px}
  .meta dd{color:#a0a0a0;margin-bottom:3px}
  .letterhead .company-name{
    position:absolute;right:40px;top:62px;font-size:34px;color:var(--letter-name);
  }
  .rule{position:absolute;height:1px;background:var(--line)}
  .rule-head{left:40px;right:40px;top:118px}
  .letter-title{
    position:absolute;left:40px;right:40px;top:146px;text-align:center;
    font-family:"Exo 2",Arial,sans-serif;font-weight:700;font-size:14px;color:var(--orange);
  }
  .rule-title{left:40px;right:40px;top:176px}
  .letter-body{position:absolute;left:40px;right:40px;top:196px;font-size:8.5px;line-height:13px;color:#8a8a8a;text-align:justify}
  .letter-body p{margin-bottom:12px}
  .rule-sign{left:40px;right:40px;top:430px}
  .signature{position:absolute;right:60px;top:478px;width:120px;height:30px;background:linear-gradient(90deg,#ececec,#f7f7f7);border-radius:4px}
  .rule-signoff{left:260px;right:40px;top:516px}
  .letterhead .contact{position:absolute;left:300px;top:538px;font-size:9px;line-height:15px;color:#8a8a8a}
  .letterhead .band{position:absolute;left:0;right:0;bottom:0;height:10px;background:var(--orange)}
</style>
</head>
<body>

<section class="folder" aria-label="Presentation folder cover">
  <div class="company-name">Lumora</div>

  <div class="contact">
    <div class="contact-row">
      <svg width="8" height="10" viewBox="0 0 8 10"><path d="M4 0a4 4 0 0 0-4 4c0 3 4 6 4 6s4-3 4-6a4 4 0 0 0-4-4z" fill="#ee7a2c"/></svg>
      <span>123, Main Street, Anytown,<br>Postal Code, Country</span>
    </div>
    <div class="contact-row">
      <svg width="8" height="9" viewBox="0 0 8 9"><path d="M1 0h2l1 2-1 1c.5 1.2 1.3 2 2.5 2.5l1-1 1.5 1v2C7 8 0 8 1 0z" fill="#ee7a2c"/></svg>
      <span>555-1234-56</span>
    </div>
    <div class="contact-row">
      <svg width="8" height="8" viewBox="0 0 8 8"><rect width="8" height="8" rx="1" fill="#ee7a2c"/></svg>
      <span>555-1234-56</span>
    </div>
    <div class="contact-row">
      <svg width="8" height="8" viewBox="0 0 8 8"><rect y="1" width="8" height="6" fill="#ee7a2c"/></svg>
      <span>we@youraddress.com</span>
    </div>
    <div class="contact-row">
      <svg width="8" height="8" viewBox="0 0 8 8"><circle cx="4" cy="4" r="4" fill="#ee7a2c"/></svg>
      <span>www.yourwebsite.com</span>
    </div>
  </div>

  <svg class="swoop" viewBox="0 0 500 200" preserveAspectRatio="none" aria-hidden="true">
    <defs>
      <linearGradient id="swoopFill" x1="0" y1="0" x2="1" y2="0">
        <stop offset="0" stop-color="#c9551a"/>
        <stop offset="1" stop-color="#f08a3a"/>
      </linearGradient>
    </defs>
    <path d="M0 60 C140 150 330 170 500 110 L500 200 L0 200 Z" fill="url(#swoopFill)"/>
    <path d="M0 60 C140 150 330 170 500 110 L500 125 C330 180 140 165 0 80 Z" fill="#4d4d4d" opacity=".55"/>
  </svg>
</section>

<section class="letterhead" aria-label="Letterhead">
  <dl class="meta">
    <dt>Subject</dt><dd>lorem ipsum</dd>
    <dt>Date</dt><dd>12/05/2014</dd>
    <dt>Adressed to</dt><dd>Anna Reyes</dd>
  </dl>

  <div class="company-name">Lumora</div>

  <div class="rule rule-head"></div>
  <h1 class="letter-title">Lorem ipsum dolor sit ametconsectetur</h1>
  <div class="rule rule-title"></div>

  <div class="letter-body">
    <p>Lorem ipsum dolor sit amet, consectetur adipiscing elit. Nulla sodales nisl vitae lorem ipsum dolor sit amet, consectetur adipiscing elit. Suspendisse feugiat eros nisi, a facilisis risus eleifend sed. Aliquam mauris enim, fermentum eu lacinia sit amet, laoreet vel leo. Nullam eleifend nulla eu bibendum porttitor. Vivamus justo tincidunt, etiam non condimentum tortor. Integer volutpat neque nec nibh tristique.</p>
    <p>Ut vitae interdum diam, in euismod ante. Pellentesque volutpat, risus sit amet sodales hendrerit, mi turpis vulputate dolor, eget cursus nulla eros nec tellus. Nulla tincidunt molestie libero vel pretium. Donec condimentum nulla sit amet risus semper imperdiet. Duis congue eros nec diam blandit, et ornare metus mattis. Nam id dui in ligula malesuada feugiat.</p>
    <p>Best regards,</p>
  </div>

  <div class="rule rule-sign"></div>
  <div class="signature" role="img" aria-label="Handwritten signature"></div>
  <div class="rule rule-signoff"></div>

  <div class="contact">
    <div class="contact-row">
      <svg width="8" height="10" viewBox="0 0 8 10"><path d="M4 0a4 4 0 0 0-4 4c0 3 4 6 4 6s4-3 4-6a4 4 0 0 0-4-4z" fill="#ee7a2c"/></svg>
      <span>123, Main Street, Anytown,<br>Postal Code, Country</span>
    </div>
    <div class="contact-row">
      <svg width="8" height="9" viewBox="0 0 8 9"><path d="M1 0h2l1 2-1 1c.5 1.2 1.3 2 2.5 2.5l1-1 1.5 1v2C7 8 0 8 1 0z" fill="#ee7a2c"/></svg>
      <span>555-1234-56</span>
    </div>
    <div class="contact-row">
      <svg width="8" height="8" viewBox="0 0 8 8"><rect width="8" height="8" rx="1" fill="#ee7a2c"/></svg>
      <span>555-1234-56</span>
    </div>
    <div class="contact-row">
      <svg width="8" height="8" viewBox="0 0 8 8"><rect y="1" width="8" height="6" fill="#ee7a2c"/></svg>
      <span>we@youraddress.com</span>
    </div>
    <div class="contact-row">
      <svg width="8" height="8" viewBox="0 0 8 8"><circle cx="4" cy="4" r="4" fill="#ee7a2c"/></svg>
      <span>www.yourwebsite.com</span>
    </div>
  </div>

  <div class="band"></div>
</section>

</body>
</html>
```